Veriplume Digital Badge Header/Banner for Nimbleway People Certificaiton

We need a new page header/banner for Veriplume https://www.badgequill.example/ where we have all our digital badges and certificates for our Nimbleway People Coaching https://www.badgequill.example/issuer/48213/credentials

https://www.badgequill.example/group/503118
https://www.badgequill.example/group/514927
https://www.badgequill.example/group/520364

https://www.brightfernpartners.example/

Target Market(s)

HR Professionals

Font styles to use
Sans Serif

```html
<!DOCTYPE html>
<html lang="en">
<head>
<meta charset="utf-8">
<title>Veriplume – Nimbleway People Badges Banner</title>
<link rel="stylesheet" href="https://fonts.googleapis.com/css2?family=Montserrat:wght@300;700&display=swap">
<style>
  :root {
    --page-bg: #ffffff;
    --banner-blue: #2f6fd6;
    --banner-indigo: #2d3596;
    --banner-violet: #5a3fbf;
    --banner-purple: #8c52de;
    --banner-lilac: #7d66e0;
    --text-light: #ffffff;
  }
  * { margin: 0; padding: 0; box-sizing: border-box; }
  html, body {
    width: 1200px;
    height: 511px;
    overflow: hidden;
    background: var(--page-bg);
  }
  .canvas {
    position: relative;
    width: 1200px;
    height: 511px;
  }
  .banner {
    position: absolute;
    left: 49px;
    top: 109px;
    width: 1102px;
    height: 293px;
    overflow: hidden;
  }
  .banner-backdrop {
    position: absolute;
    inset: 0;
    background:
      radial-gradient(ellipse 45% 70% at 8% 30%, rgba(60, 150, 240, 0.85), transparent 70%),
      radial-gradient(ellipse 50% 60% at 85% 80%, rgba(150, 90, 230, 0.8), transparent 70%),
      radial-gradient(ellipse 60% 40% at 50% 100%, rgba(130, 110, 225, 0.7), transparent 75%),
      linear-gradient(100deg, var(--banner-blue) 0%, var(--banner-indigo) 40%, var(--banner-violet) 65%, var(--banner-purple) 88%, var(--banner-lilac) 100%);
  }
  .banner-headline {
    position: absolute;
    inset: 0;
    display: flex;
    flex-direction: column;
    align-items: center;
    color: var(--text-light);
    font-family: "Montserrat", sans-serif;
    text-align: center;
    text-transform: uppercase;
  }
  .headline-intro {
    margin-top: 56px;
    font-weight: 300;
    font-size: 42px;
    line-height: 46px;
    letter-spacing: 0.24em;
    padding-left: 0.24em;
  }
  .headline-main {
    margin-top: 9px;
    font-weight: 700;
    font-size: 60px;
    line-height: 66px;
    letter-spacing: 0.005em;
    white-space: nowrap;
  }
</style>
</head>
<body>
  <main class="canvas">
    <section class="banner">
      <div class="banner-backdrop" role="img" aria-label="Blue to purple abstract technology backdrop with glowing circuit lines and network nodes"></div>
      <h1 class="banner-headline">
        <span class="headline-intro">We have all our</span>
        <span class="headline-main">Digital Badges &amp; Certificates</span>
        <span class="headline-main">For our Nimbleway People</span>
      </h1>
    </section>
  </main>
</body>
</html>
```